Career Management Consultant Fun Professional Business Card

This is a business card for a personal career management consultant. The vibe needs to be professional but fun, modern with colour.

The name of the business is "Marcus Holloway Career Management Consulting"

The name of the individual is "Marcus Holloway" and his title is "Career Management Consultant"

Contact Information for Business Card

Marcus Holloway
Phone: 0400 872 316
Email: Marcus.Holloway@veltrimail.com

```html
<!DOCTYPE html>
<html lang="en">
<head>
<meta charset="utf-8">
<title>Marcus Holloway – Business Card</title>
<link rel="stylesheet" href="https://fonts.googleapis.com/css2?family=Questrial&family=Tinos:wght@700&display=swap">
<style>
  :root {
    --teal: #45a8c3;
    --teal-deep: #3a9bb6;
    --white: #ffffff;
    --paper: #ecedee;
    --shadow: rgba(20, 40, 50, 0.18);
  }
  * { margin: 0; padding: 0; box-sizing: border-box; }
  html, body { width: 1200px; height: 945px; overflow: hidden; }
  body {
    background: var(--paper);
    position: relative;
    font-family: "Questrial", sans-serif;
  }
  .card {
    position: absolute;
    width: 540px;
    height: 309px;
    overflow: hidden;
    box-shadow: 0 10px 28px var(--shadow);
  }
  .card--back { left: 40px; top: 318px; background: var(--white); }
  .card--front { left: 620px; top: 318px; background: var(--teal); }

  /* back side */
  .back-bands { position: absolute; inset: 0; }
  .back-mark {
    position: absolute; left: 168px; top: 46px;
    width: 84px; height: 84px; border-radius: 50%;
    background: var(--teal);
  }
  .back-name {
    position: absolute; left: 40px; top: 138px;
    font-size: 38px; letter-spacing: 1.5px;
    color: var(--teal); text-transform: uppercase; white-space: nowrap;
  }
  .back-tagline {
    position: absolute; left: 40px; width: 430px; top: 182px;
    text-align: right; font-size: 10px; letter-spacing: 0.6px;
    color: var(--teal); text-transform: uppercase;
  }
  .contact {
    position: absolute; left: 200px; top: 210px;
    list-style: none; color: var(--teal);
    font-size: 15px; letter-spacing: 0.6px; text-transform: uppercase;
  }
  .contact li { display: flex; align-items: center; gap: 8px; margin-bottom: 8px; }
  .contact svg { width: 15px; height: 15px; flex: none; }

  /* front side */
  .front-mark {
    position: absolute; left: 22px; top: 72px;
    width: 172px; height: 172px; border-radius: 50%;
    background: var(--white);
  }
  .front-name {
    position: absolute; left: 204px; top: 92px;
    font-family: "Tinos", serif; font-weight: 700;
    font-size: 38px; color: var(--white); white-space: nowrap;
  }
  .front-rule {
    position: absolute; left: 190px; top: 138px;
    width: 330px; height: 5px; background: var(--white);
  }
  .front-tagline {
    position: absolute; left: 206px; top: 148px;
    font-size: 10.5px; letter-spacing: 0.8px;
    color: var(--white); text-transform: uppercase;
  }
</style>
</head>
<body>
  <section class="card card--back" aria-label="Card back">
    <svg class="back-bands" viewBox="0 0 540 309" preserveAspectRatio="none" aria-hidden="true">
      <rect width="540" height="309" fill="var(--teal)"/>
      <polygon points="0,120 540,20 540,262 0,300" fill="var(--white)"/>
      <polygon points="0,300 540,262 540,272 0,309" fill="var(--teal-deep)"/>
    </svg>
    <div class="back-mark" aria-hidden="true"></div>
    <h1 class="back-name">Marcus Holloway</h1>
    <p class="back-tagline">Career Management Consulting</p>
    <ul class="contact">
      <li>
        <svg viewBox="0 0 16 16" aria-hidden="true"><rect width="16" height="16" rx="2" fill="var(--teal)"/><path d="M5 3.5l1.6 2.4-1 1a6 6 0 0 0 3.5 3.5l1-1 2.4 1.6-.9 1.6C8 12.6 3.4 8 3.4 4.4z" fill="var(--white)"/></svg>
        0400 872 316
      </li>
      <li>
        <svg viewBox="0 0 16 16" aria-hidden="true"><rect width="16" height="16" rx="2" fill="var(--teal)"/><circle cx="8" cy="8" r="2.4" fill="none" stroke="var(--white)" stroke-width="1.4"/><path d="M10.4 6v3a1.4 1.4 0 0 0 2.6 0V8a5 5 0 1 0-2 4" fill="none" stroke="var(--white)" stroke-width="1.4"/></svg>
        Marcus.Holloway@veltrimail.com
      </li>
    </ul>
  </section>

  <section class="card card--front" aria-label="Card front">
    <div class="front-mark" aria-hidden="true"></div>
    <h2 class="front-name">Marcus Holloway</h2>
    <div class="front-rule" aria-hidden="true"></div>
    <p class="front-tagline">Career Management Consulting</p>
  </section>
</body>
</html>
```